Brightfen Business Card Redesign & Logo Update

We need to update our business cards to something more modern and fresh. Brightfen can provide the current color schemes and old design examples, but welcome creativity in helping us with this redesign. PLEASE NOTE that we no longer utilize the "tree" and/or "leaf" imagery in our branding. If able would apprecaite an update on the quality of our "words only" logo in Ai. / PNG formats too.

Target Market(s)

Investors, landowners, corporate partners, contractors

Industry/Entity Type

Environmental Restoration & Conservation

Contact Information for Business Card

Logo, persons name, title, mailing address, phone and email, website url

Font styles to use
Other font styles liked:
• Merriweather

Requirements
Nice to have
• Logo, persons name, title, mailing address, phone and email, website url, but open to ideams
Should not have
• No all back backgrounds

```html
<!DOCTYPE html>
<html lang="en">
<head>
<meta charset="utf-8">
<title>Brightfen Business Card</title>
<link rel="stylesheet" href="https://fonts.googleapis.com/css2?family=Montserrat:wght@400;500;800&display=swap">
<style>
  :root {
    --bg: #e4e4e4;
    --card: #ffffff;
    --orange: #ea7c22;
    --green: #16803f;
    --ink: #1a1a1a;
  }
  * { margin: 0; padding: 0; box-sizing: border-box; }
  html, body { width: 1200px; height: 856px; overflow: hidden; }
  body {
    background: var(--bg);
    font-family: "Montserrat", sans-serif;
    color: var(--ink);
    position: relative;
  }
  .card {
    position: absolute;
    top: 270px;
    width: 540px;
    height: 309px;
    background: var(--card);
    border-bottom: 4px solid var(--orange);
    box-shadow: 0 6px 18px rgba(0,0,0,0.18);
  }
  .card--front { left: 40px; }
  .card--back { left: 620px; }

  .wordmark {
    font-weight: 800;
    color: var(--green);
    letter-spacing: 0.5px;
    line-height: 1;
  }
  .card--front .wordmark {
    position: absolute;
    top: 42px;
    right: 40px;
    font-size: 40px;
  }
  .address {
    position: absolute;
    top: 124px;
    right: 40px;
    text-align: right;
    font-size: 13px;
    line-height: 1.5;
  }
  .person {
    position: absolute;
    top: 112px;
    left: 40px;
  }
  .person__name {
    font-size: 17px;
    font-weight: 800;
    color: var(--orange);
    letter-spacing: 0.5px;
  }
  .person__name .first { color: var(--green); }
  .person__title {
    font-size: 13px;
    margin-top: 4px;
  }
  .contacts {
    position: absolute;
    left: 40px;
    bottom: 36px;
    list-style: none;
  }
  .contacts li {
    display: flex;
    align-items: center;
    gap: 10px;
    font-size: 14px;
    margin-top: 7px;
  }
  .contacts svg { width: 20px; height: 20px; flex: none; }

  .card--back .wordmark {
    position: absolute;
    left: 0; right: 0;
    top: 50%;
    transform: translateY(-50%);
    text-align: center;
    font-size: 76px;
  }
</style>
</head>
<body>

<section class="card card--front">
  <div class="wordmark">Brightfen</div>
  <div class="address">42-10 Alder Rd 7<br>Fernbrook, NY 10990</div>
  <div class="person">
    <div class="person__name"><span class="first">DANA</span> WHITLOCK</div>
    <div class="person__title">Managing Director</div>
  </div>
  <ul class="contacts">
    <li>
      <svg viewBox="0 0 20 20" aria-hidden="true"><circle cx="10" cy="10" r="10" fill="var(--orange)"/><path d="M7 5.5l2 2-1 1.2c.6 1.3 1.6 2.3 2.9 2.9l1.2-1 2 2-1.3 1.6C9.5 14 6 10.5 5.6 6.8z" fill="#fff"/></svg>
      555-014-2260
    </li>
    <li>
      <svg viewBox="0 0 20 20" aria-hidden="true"><circle cx="10" cy="10" r="10" fill="var(--orange)"/><rect x="5" y="6.5" width="10" height="7" fill="none" stroke="#fff" stroke-width="1.3"/><path d="M5 6.5l5 4 5-4" fill="none" stroke="#fff" stroke-width="1.3"/></svg>
      info@brightfen.com
    </li>
    <li>
      <svg viewBox="0 0 20 20" aria-hidden="true"><circle cx="10" cy="10" r="10" fill="var(--orange)"/><circle cx="10" cy="10" r="5" fill="none" stroke="#fff" stroke-width="1.3"/><path d="M5 10h10M10 5c-2 2.6-2 7.4 0 10M10 5c2 2.6 2 7.4 0 10" fill="none" stroke="#fff" stroke-width="1"/></svg>
      www.brightfen.com
    </li>
  </ul>
</section>

<section class="card card--back">
  <div class="wordmark">Brightfen</div>
</section>

</body>
</html>
```